Bramblewood Joinery Website

My client Bramblewood Joinery is looking for a redesign for a Word Press Website. Their current site is at www.bramblewoodjoinery.example They are a custom cabinet company, but also create bathroom, living room, bar and entertainment and bedroom cabinets too. They would like a design that emulates the master craftsman work they do yet a contemporary style.

Their current site was designed using Flash elements.

Target Market(s)

Home owners and builders of high end homes

Industry/Entity Type

Entertainment

Font styles to use
Serif
Decorative

Requirements
Must have
• Must show their work and logo using a contemporary style.
Nice to have
• Sliders that showcase their projects.

```html
<!DOCTYPE html>
<html lang="en">
<head>
<meta charset="utf-8">
<title>Bramblewood Joinery</title>
<link rel="stylesheet" href="https://fonts.googleapis.com/css2?family=Raleway:wght@500;600&family=Lato:wght@300;400;700&display=swap">
<style>
:root{
  --green:#16881a;
  --green-dark:#0f6e13;
  --black:#111;
  --page:#ffffff;
  --backdrop:#dcd8d2;
  --panel:#efefef;
  --text:#555;
  --heading:#222;
  --footer:#464646;
  --footer-top:#383838;
  --footer-text:#bdbdbd;
  --footer-head:#e2e2e2;
}
*{margin:0;padding:0;box-sizing:border-box}
html,body{width:1200px;height:1200px;overflow:hidden}
body{position:relative;background:var(--backdrop);font-family:"Lato",sans-serif;color:var(--text)}
.backdrop-photo{position:absolute;left:0;top:85px;width:1200px;height:328px;background:linear-gradient(90deg,#cfc8bf 0%,#ebe7e1 8%,#e4e0da 92%,#cfc9c1 100%)}
.backdrop-fade{position:absolute;left:0;top:413px;width:1200px;height:517px;background:linear-gradient(#ece9e4,#f4f2ee)}
.page{position:absolute;left:95px;top:0;width:1010px;height:930px;background:var(--page);box-shadow:0 0 12px rgba(0,0,0,.15)}
.masthead{position:absolute;left:110px;top:0;width:980px;height:86px;background:linear-gradient(#1c1c1c,#0b0b0b)}
.brand{position:absolute;left:124px;top:0;width:130px;height:130px;border-radius:50%;background:var(--black);display:flex;align-items:center;justify-content:center;text-align:center;color:#fff;font-family:"Lato",sans-serif;font-weight:700;font-size:15px;line-height:1.2;padding:18px;z-index:3}
.utility-nav{position:absolute;right:135px;top:14px;display:flex;gap:22px;font-size:14px;color:#aaa}
.main-nav{position:absolute;right:134px;top:47px;display:flex;gap:41px;font-size:16px;color:#fff}
.main-nav .active{position:relative}
.main-nav .active::after{content:"";position:absolute;left:-3px;right:-3px;top:33px;height:4px;background:var(--green)}
.hero{position:absolute;left:110px;top:86px;width:980px;height:328px;background:linear-gradient(160deg,#e6e2dc 0%,#cfc7bc 40%,#7a4a30 75%,#4a2c1c 100%)}
.hero-title{position:absolute;left:110px;top:190px;width:962px;text-align:center;font-family:"Raleway",sans-serif;font-weight:600;font-size:40px;line-height:40px;color:#fff;text-shadow:0 2px 6px rgba(0,0,0,.6)}
.arrow{position:absolute;top:211px;width:45px;height:45px;border-radius:50%;background:var(--green)}
.arrow svg{display:block}
.arrow-prev{left:119px}.arrow-next{left:1036px}
.tabs-panel{position:absolute;left:110px;top:454px;width:980px;height:318px;background:var(--panel)}
.tab-marker{position:absolute;left:0;top:0;width:245px;height:8px;background:var(--green)}
.tab-list{position:absolute;left:23px;top:19px;width:935px;height:30px;border-bottom:1px solid #999;font-size:15px;font-weight:700;color:#222}
.tab-list span{position:absolute;top:0}
.intro{position:absolute;left:21px;top:112px;width:410px}
.intro h2{font-family:"Raleway",sans-serif;font-weight:500;font-size:22px;color:var(--heading);margin-bottom:14px}
.intro p{font-size:13.5px;font-weight:300;line-height:20px;color:#555;padding-left:2px}
.intro a{display:block;margin-top:8px;padding-left:2px;font-size:13.5px;color:var(--green);text-decoration:none}
.work{position:absolute;top:71px;width:232px;height:217px;background:#fff;box-shadow:0 1px 4px rgba(0,0,0,.25);padding:6px}
.work div{width:100%;height:100%}
.work-1{left:473px}.work-1 div{background:linear-gradient(135deg,#5a4a3c,#2a1f18 55%,#6b4a2f)}
.work-2{left:727px}.work-2 div{background:linear-gradient(160deg,#bfb6a8,#8e8272 50%,#2e2a26)}
.cta-band{position:absolute;left:110px;top:808px;width:979px;height:82px;background:var(--green);display:flex;align-items:center;color:#fff;font-size:16px;line-height:20px;text-align:center}
.cta-band div{height:60px;display:flex;align-items:center;justify-content:center}
.cta-band div+div{border-left:1px solid rgba(255,255,255,.8)}
.footer{position:absolute;left:0;top:930px;width:1200px;height:270px;background:var(--footer);border-top:15px solid var(--footer-top)}
.col{position:absolute;top:48px}
.col h3{font-weight:400;font-size:15px;color:var(--footer-head);display:flex;align-items:center;gap:8px;margin-bottom:22px}
.col h3::after{content:"";flex:1;border-top:1px solid #666;border-bottom:1px solid #3b3b3b}
.col li{list-style:none;font-size:12px;line-height:20px;color:var(--footer-text)}
.contact li{line-height:23px}
.social{display:flex;gap:13px;margin-bottom:26px}
.social span{width:33px;height:33px;border-radius:3px;background:#2f6fb0}
.social span:nth-child(2){background:#49a8d8}
.newsletter{display:flex;height:34px;background:#2b2b2b;border-radius:3px;padding:3px;align-items:center}
.newsletter span{flex:1;font-size:11px;font-style:italic;color:#888;padding-left:9px}
.newsletter b{font-weight:400;font-size:13px;color:#fff;background:#111;border:1px solid #666;padding:5px 13px;border-radius:2px}
</style>
</head>
<body>
<div class="backdrop-photo" role="img" aria-label="Faded photo of a white kitchen interior"></div>
<div class="backdrop-fade"></div>
<div class="page"></div>

<header class="masthead">
</header>
<div class="brand">Bramblewood Joinery</div>
<nav class="utility-nav"><span>Who We Are</span><span>Getting Started</span><span>Contact Us</span></nav>
<nav class="main-nav"><span class="active">Home</span><span>Customer Experience</span><span>Professional</span><span>Portfolio</span><span>Cabinet Hardware</span></nav>

<section class="hero" role="img" aria-label="Photo of a white custom kitchen with red bar stools and a wooden floor"></section>
<h1 class="hero-title">Kansas City's Premier Custom<br>Kitchen Cabinet Design Company</h1>
<span class="arrow arrow-prev"><svg width="45" height="45"><path d="M26 14 L17 22.5 L26 31" fill="none" stroke="#fff" stroke-width="3"/></svg></span>
<span class="arrow arrow-next"><svg width="45" height="45"><path d="M19 14 L28 22.5 L19 31" fill="none" stroke="#fff" stroke-width="3"/></svg></span>

<section class="tabs-panel">
  <div class="tab-marker"></div>
  <div class="tab-list">
    <span style="left:56px">Who We Are</span>
    <span style="left:292px">Our Portfolio</span>
    <span style="left:523px;top:1px">Professional</span>
    <span style="left:718px">Customer Experience</span>
  </div>
  <div class="intro">
    <h2>Who We Are</h2>
    <p>Established in 1966, Bramblewood Joinery has long stood as one of the Midwest's most renowned makers of custom cabinets and fixtures. Our handcrafted, award-winning creations have been chosen by hundreds of noteworthy homebuilders.</p>
    <a href="#">View More &gt;&gt;</a>
  </div>
  <figure class="work work-1"><div role="img" aria-label="Photo of a dark wood kitchen island"></div></figure>
  <figure class="work work-2"><div role="img" aria-label="Photo of a white kitchen with range hood and pendant lights"></div></figure>
</section>

<section class="cta-band">
  <div style="width:245px">SEE ALL<br>NEW DISIGNS</div>
  <div style="width:250px">FIND US ON<br>FRIENDWALL</div>
  <div style="width:260px">VOEW OUR<br>CATALOG</div>
  <div style="width:224px">CABINET<br>HARDWARE</div>
</section>

<footer class="footer">
  <div class="col contact" style="left:128px;width:155px">
    <h3>Contact Info</h3>
    <ul><li>Lorem ipsum dolor sit amet,</li><li>consectetur adipisicing elit,</li><li>Phone: 08 5550 1927</li><li style="font-size:13px">hello@bramblewood.example</li></ul>
  </div>
  <div class="col" style="left:334px;width:210px">
    <h3>Topic</h3>
    <ul><li>Advice</li><li>About</li><li>Contact</li><li>Privacy Policy</li><li>Terms &amp; Conditons</li></ul>
  </div>
  <div class="col" style="left:593px;width:155px">
    <h3>Company Info</h3>
    <ul style="font-size:11px"><li>Home</li><li>Product &amp; Services</li><li>Quality</li><li>Carrers</li><li>Contact Us</li></ul>
  </div>
  <div class="col" style="left:798px;width:266px">
    <h3 style="margin-bottom:20px">Stay updates on our Socail Network</h3>
    <div class="social"><span></span><span></span><span></span></div>
    <h3 style="margin-bottom:12px">Join Our Newsletter</h3>
    <div class="newsletter"><span>Enter your email address</span><b>Subscribe</b></div>
  </div>
</footer>
</body>
</html>
```